Australian Trucking Company Requires Professional Looking Stationary

We require a professional looking stationary design that incorporates our newly designed logo.

Our business, called "Brell Haulage Contracting", provides contracting work, transport and logistics to business in Western Australia particularly with links to the mining sector.

We are a small business looking to expand and our new logo and our new stationary will help develop our brand image in our market place.

Target Market(s)

Businesses and Corporation with links to the Mining Sector

Industry/Entity Type

Small Business

Requirements
Must have
• The letterhead must have the following details:
The new logo

Text saying: "Brell Holdings Pty Ltd (ACN 582 316 907) ATF The Brell Discretionary Trust T/AS"
"ABN 71 834 209 553"
Address "P.O Box 817 Wattlegrove WA, 6958"
Phone: 08 9352 7140
Email: brellhaul@mailbox-example.com.au

The text on the letterhead should be editable as the details are likely to change in the near future. Provision should be made for a website address all though one isn't available at the moment.

The styling, layout and font text is entirely up to the designer.

```html
<!DOCTYPE html>
<html lang="en">
<head>
<meta charset="utf-8">
<title>Brell Haulage Contracting – Business Card</title>
<link href="https://fonts.googleapis.com/css2?family=Open+Sans:wght@400;600;700;800&display=swap" rel="stylesheet">
<style>
  :root {
    --bg: #ece9e4;
    --card: #ffffff;
    --red: #c8161d;
    --red-dark: #8e0c12;
    --red-light: #e0262c;
    --grey-band-1: #d9d9d9;
    --grey-band-2: #9a9a9a;
    --ink: #3a3a3a;
    --ink-soft: #555555;
    --truck-1: #8a8a8a;
    --truck-2: #4a4a4a;
    --white: #ffffff;
  }
  * { box-sizing: border-box; margin: 0; padding: 0; }
  html, body { width: 1200px; height: 407px; overflow: hidden; }
  body {
    background: var(--bg);
    font-family: "Open Sans", Arial, sans-serif;
    color: var(--ink);
    position: relative;
  }
  .card {
    position: absolute;
    top: 60px;
    width: 504px;
    height: 288px;
    background: var(--card);
    box-shadow: 0 2px 6px rgba(0,0,0,0.18);
    overflow: hidden;
  }
  .card--front { left: 58px; }
  .card--back { left: 638px; }
  .swoosh { position: absolute; inset: 0; width: 504px; height: 288px; }

  .truck-art {
    position: absolute;
    background: radial-gradient(ellipse at 55% 45%, var(--truck-1), var(--truck-2));
    border-radius: 6px;
    opacity: 0.85;
  }
  .card--front .truck-art { left: 28px; top: 30px; width: 84px; height: 78px; }
  .card--back .truck-art { left: 32px; top: 142px; width: 168px; height: 130px; }

  .brand-name {
    position: absolute;
    left: 130px;
    top: 36px;
    color: var(--red);
    font-weight: 800;
    font-size: 23px;
    line-height: 24px;
    text-transform: uppercase;
    letter-spacing: 0.5px;
  }

  .holder {
    position: absolute;
    left: 31px;
    top: 222px;
    font-size: 10.5px;
    line-height: 20px;
    color: var(--ink-soft);
  }
  .holder__name { font-size: 16px; font-weight: 700; color: var(--ink); line-height: 20px; }
  .holder__title { font-size: 11px; font-weight: 400; color: var(--ink-soft); }

  .contact {
    position: absolute;
    right: 14px;
    top: 234px;
    list-style: none;
    text-align: right;
    color: var(--white);
    font-size: 10.5px;
    line-height: 17px;
  }
  .contact li { display: flex; justify-content: flex-end; align-items: center; gap: 8px; }
  .contact svg { width: 10px; height: 10px; flex: none; }

  .legal-line {
    position: absolute;
    left: 29px;
    top: 32px;
    font-size: 10.5px;
    color: var(--ink-soft);
  }
  .web-address {
    position: absolute;
    right: 28px;
    top: 255px;
    color: var(--white);
    font-weight: 700;
    font-size: 13px;
    letter-spacing: 2.4px;
  }
</style>
</head>
<body>

<section class="card card--front">
  <svg class="swoosh" viewBox="0 0 504 288" aria-hidden="true">
    <defs>
      <linearGradient id="band-front" x1="0" y1="1" x2="1" y2="0">
        <stop offset="0" stop-color="var(--grey-band-1)"/>
        <stop offset="1" stop-color="var(--grey-band-2)"/>
      </linearGradient>
      <radialGradient id="red-front" cx="0.35" cy="0.75" r="0.9">
        <stop offset="0" stop-color="var(--red-light)"/>
        <stop offset="1" stop-color="var(--red-dark)"/>
      </radialGradient>
    </defs>
    <path d="M150 288 C310 240 430 140 470 0 L504 0 L504 40 C440 150 330 250 195 288 Z" fill="url(#band-front)"/>
    <path d="M195 288 C330 250 440 150 504 40 L504 288 Z" fill="url(#red-front)"/>
  </svg>

  <div class="truck-art" role="img" aria-label="Illustration of a prime mover truck in grey"></div>
  <div class="brand-name">Brell<br>Haulage<br>Contracting</div>

  <div class="holder">
    <div class="holder__name">Your Name <span class="holder__title">/ Title</span></div>
    <div>ABN 71 834 209 553</div>
    <div>P.O Box 817 Wattlegrove WA, 6958</div>
  </div>

  <ul class="contact">
    <li>08 9352 7140
      <svg viewBox="0 0 10 10"><circle cx="5" cy="5" r="4.3" fill="none" stroke="#fff" stroke-width="1"/><path d="M3.3 2.8 L4.3 2.6 L4.7 3.9 L4.1 4.4 Q4.6 5.5 5.6 5.9 L6.1 5.3 L7.3 5.7 L7.2 6.7 Q4.2 7 3.3 2.8Z" fill="#fff"/></svg>
    </li>
    <li>brellhaul@mailbox-example.com.au
      <svg viewBox="0 0 10 10"><rect x="0.5" y="2" width="9" height="6" fill="#fff"/><path d="M0.5 2 L5 5.5 L9.5 2" fill="none" stroke="#b01218" stroke-width="0.8"/></svg>
    </li>
    <li>www.brellhaulage.com.au
      <svg viewBox="0 0 10 10"><circle cx="5" cy="5" r="4.5" fill="#fff"/><path d="M0.5 5 H9.5 M5 0.5 V9.5" stroke="#b01218" stroke-width="0.7"/></svg>
    </li>
  </ul>
</section>

<section class="card card--back">
  <svg class="swoosh" viewBox="0 0 504 288" aria-hidden="true">
    <defs>
      <linearGradient id="band-back" x1="0" y1="1" x2="1" y2="0">
        <stop offset="0" stop-color="var(--grey-band-1)"/>
        <stop offset="1" stop-color="var(--grey-band-2)"/>
      </linearGradient>
      <radialGradient id="red-back" cx="0.3" cy="0.8" r="0.9">
        <stop offset="0" stop-color="var(--red-light)"/>
        <stop offset="1" stop-color="var(--red-dark)"/>
      </radialGradient>
    </defs>
    <path d="M140 288 C310 240 440 140 495 0 L504 0 L504 40 C440 150 330 250 185 288 Z" fill="url(#band-back)"/>
    <path d="M185 288 C330 250 440 150 504 40 L504 288 Z" fill="url(#red-back)"/>
  </svg>

  <p class="legal-line">Brell Holdings Pty Ltd (ACN 582 316 907) ATF The Brell Discretionary Trust T/AS</p>
  <div class="truck-art" role="img" aria-label="Large grey illustration of a prime mover truck"></div>
  <p class="web-address">www.brellhaulage.com.au</p>
</section>

</body>
</html>
```